Explosive, chemical reaction of creativity!

Web design for a digital marketing company. The unconventional is encouraged!
This is for a cool, young, geographically diverse company (sketchhive... you are all part of our team!!!)... we build websites but our real specialty is "search experience optimization".... creating conversion focused content, SEO (including content), and social media.

Target Market(s)

small to medium size businesses, law firms, medical practices, municipalities

Industry/Entity Type

Marketing

Number of Pages Required

2 page

Requirements
Must have
• WOW
• something different and special... we've been playing with a science theme (www.fernquillmedia.marketing) but we are open to different looks, layouts, etc.
• we nee a homepage design and an interior page design
• content needs to include: Marketing Catalysts (about us), Our Formula (services), Chemical Reactions(Results/Our Clients),
• FREE Online Prism Check
• Let us put together an objective snapshot of your digital presence for you.
Nice to have
• we are open to the use of background video (chemical reaction???)
• we are open to cool and different imagery
Should not have
• template look like most other websites

```html
<!DOCTYPE html>
<html lang="en">
<head>
<meta charset="utf-8">
<title>Fernquill Digital Marketing</title>
<link rel="stylesheet" href="https://fonts.googleapis.com/css2?family=Roboto:ital,wght@0,400;0,500;0,700;1,400&family=Oswald:wght@500;600&display=swap">
<style>
:root{
  --blue:#1a66b0;
  --blue-deep:#0f4f91;
  --navy:#0d2744;
  --navy-dark:#081a2e;
  --ink:#222;
  --muted:#666;
  --line:#d7dde4;
  --white:#fff;
  --footer:#0b0d10;
}
*{box-sizing:border-box;margin:0;padding:0}
html,body{width:1200px;height:3056px;overflow:hidden}
body{font-family:"Roboto",Arial,sans-serif;color:var(--ink);background:var(--white);position:relative}
.abs{position:absolute}
.brand{display:flex;align-items:center;gap:10px;font-family:"Roboto",Arial,sans-serif;font-weight:700;font-size:17px;letter-spacing:.5px;text-transform:uppercase;white-space:nowrap}
.brand-mark{width:16px;height:16px;background:currentColor;flex:none}

/* header */
.site-header{left:0;top:0;width:1200px;height:96px;border-top:4px solid var(--blue);background:var(--white)}
.site-header .brand{position:absolute;left:98px;top:34px;color:var(--navy)}
.main-nav{position:absolute;left:510px;width:594px;top:38px;display:flex;justify-content:space-between;font-size:13px;text-transform:uppercase;color:#333;white-space:nowrap}
.main-nav a{color:inherit;text-decoration:none;padding-bottom:8px}
.main-nav a.active{color:var(--blue);border-bottom:2px solid var(--blue)}

/* hero */
.hero{left:0;top:96px;width:1200px;height:529px;background:linear-gradient(90deg,#1b2a3c 0%,#1f4a78 45%,#2a6aa8 100%)}
.hero-visual{position:absolute;left:0;top:0;width:600px;height:529px;background:radial-gradient(circle at 60% 55%,#4fb5e8 0%,#1f5f95 40%,#1a2a3c 80%)}
.hero-copy{position:absolute;left:660px;top:120px;color:var(--white)}
.hero-copy .brand{font-size:18px}
.hero-title{font-family:"Oswald",Arial,sans-serif;font-weight:600;font-size:52px;letter-spacing:1px;margin-top:26px;line-height:1}
.hero-lead{font-weight:700;font-size:16px;line-height:24px;margin-top:14px;width:460px}
.btn-outline{display:inline-flex;align-items:center;gap:14px;border:1px solid rgba(255,255,255,.8);color:var(--white);font-size:14px;font-weight:500;padding:16px 22px;margin-top:36px}
.hero-arrows{position:absolute;left:1060px;top:455px}

/* data section */
.data{left:96px;top:625px;width:1008px}
.section-title{font-size:26px;font-weight:500;color:var(--blue-deep);text-transform:uppercase;letter-spacing:.5px}
.section-kicker{font-size:11px;color:var(--muted);text-transform:uppercase;margin-top:12px}
.data p{font-size:11.5px;line-height:24px;color:var(--muted);margin-top:10px}
.data p a{color:var(--blue);text-decoration:none}
.stat-rings{position:absolute;top:250px;left:0;width:1008px}
.ring{position:absolute;width:220px}
.ring svg{display:block}
.ring-value{position:absolute;left:0;top:0;width:110px;height:110px;display:flex;align-items:center;justify-content:center;font-size:28px;font-weight:700;color:var(--blue)}
.ring-label{font-size:13px;line-height:26px;color:var(--blue);margin-top:10px}

/* prism check */
.prism{left:0;top:1075px;width:1200px;height:245px;background:linear-gradient(90deg,#0b2a4c,#14375e 50%,#0c2542);color:var(--white);text-align:center}
.prism h2{font-family:"Oswald",Arial,sans-serif;font-weight:500;font-size:26px;margin-top:42px;letter-spacing:.5px}
.prism p{font-size:12px;line-height:22px;width:860px;margin:14px auto 0;color:#dfe7f0}
.prism .actions{display:flex;justify-content:center;gap:10px;margin-top:28px}
.prism .actions span{border:1px solid rgba(255,255,255,.75);font-size:12px;padding:12px 16px}

/* formula */
.formula{left:96px;top:1320px;width:1008px;height:515px}
.formula .section-title{margin-top:30px}
.formula-visual{position:absolute;left:2px;top:130px;width:430px;height:345px;border-radius:10px;background:linear-gradient(180deg,#0a1f3a,#123a6a 60%,#c9cdd2 85%,#e4e6e9)}
.service{position:absolute;left:528px;width:480px;display:flex;gap:28px}
.service-icon{flex:none;width:78px;height:78px;border-radius:50%;background:var(--blue);border:4px solid #cfe0f0;display:flex;align-items:center;justify-content:center}
.service h3{font-size:14px;font-weight:700;color:#222;text-transform:uppercase;margin-top:8px}
.service p{font-size:11.5px;line-height:22px;color:var(--muted);margin-top:12px}

/* numbers */
.numbers{left:0;top:1835px;width:1200px;height:315px;background:linear-gradient(90deg,#1f6bb2,#2b7bc4 50%,#1d67ae);color:var(--white)}
.number{position:absolute;top:90px;width:240px;text-align:center;transform:translateX(-50%)}
.number strong{display:block;font-size:22px;font-weight:700;margin-top:16px}
.number h4{font-size:14px;font-weight:700;text-transform:uppercase;margin-top:8px;line-height:24px}
.number p{font-size:11.5px;font-style:italic;line-height:20px;margin-top:6px;color:#e6eef8}

/* snapshot */
.snapshot{left:96px;top:2150px;width:1008px;height:430px}
.snapshot h2{font-size:26px;font-weight:500;color:var(--blue-deep);line-height:34px;width:620px;margin-top:48px}
.snapshot p{font-size:11.5px;line-height:22px;color:var(--muted);width:650px;margin-top:22px}
.snapshot-device{position:absolute;left:760px;top:64px;width:246px;height:366px;border-radius:28px 28px 0 0;background:linear-gradient(180deg,#f1f3f6,#e4e8ee)}

/* footer */
.site-footer{left:0;top:2580px;width:1200px;height:410px;background:radial-gradient(circle at 80% 40%,#1b222a,var(--footer) 70%);color:var(--white)}
.site-footer .brand{position:absolute;left:98px;top:48px;color:var(--white)}
.social{position:absolute;right:96px;top:46px;display:flex;gap:6px}
.social span{width:28px;height:28px;border:1.5px solid #cfd3d8;border-radius:50%}
.footer-rule{position:absolute;left:96px;top:122px;width:1008px;height:1px;background:#2a3036}
.footer-col{position:absolute;top:162px}
.footer-col h5{font-size:16px;font-weight:700;text-transform:uppercase}
.footer-col ul{list-style:none;margin-top:20px;font-size:13px;line-height:26px;color:var(--white)}
.contact-row{display:flex;gap:12px;font-size:13px;line-height:22px;margin-top:16px}
.contact-row svg{flex:none;margin-top:4px}
.contact-form{position:absolute;left:637px;top:157px;width:467px}
.field{position:absolute;height:36px;border:1px solid #5d6670;border-radius:3px;font-size:12px;padding:10px 10px;color:#e8e8e8}
.send{position:absolute;left:0;top:170px;width:120px;height:40px;background:var(--blue);border:1px solid #7fb0e0;border-radius:3px;font-size:12px;color:var(--white);display:flex;align-items:center;justify-content:center;text-transform:uppercase}

.copyright{left:0;top:2990px;width:1200px;height:66px;background:var(--blue);color:var(--white);font-size:12px;display:flex;align-items:center;justify-content:center}
.copyright .code{position:absolute;right:46px}
</style>
</head>
<body>

<header class="site-header abs">
  <div class="brand"><span class="brand-mark"></span>Fernquill Digital Marketing</div>
  <nav class="main-nav">
    <a class="active">Home</a><a>Marketing Catalysts</a><a>Our Formula</a><a>Chemical Reactions</a><a>Contact Us</a>
  </nav>
</header>

<section class="hero abs">
  <div class="hero-visual" role="img" aria-label="Businessman holding a glowing tablet with floating marketing icons and a globe"></div>
  <div class="hero-copy">
    <div class="brand"><span class="brand-mark"></span>Fernquill Digital Marketing</div>
    <h1 class="hero-title">DIGITAL MARKETING</h1>
    <p class="hero-lead">Sed ut perspiciatis unde omnis iste natus error sit voluptatem accusantium doloremque laudantium, totam...</p>
    <span class="btn-outline">CLICK READ MORE
      <svg width="8" height="12" viewBox="0 0 8 12"><path d="M1 1l5 5-5 5" stroke="#fff" stroke-width="2" fill="none"/></svg></span>
  </div>
  <svg class="hero-arrows" width="44" height="40" viewBox="0 0 44 40"><path d="M14 4L4 20l10 16M30 4l10 16-10 16" stroke="#cfd9e6" stroke-width="1.5" fill="none"/></svg>
</section>

<section class="data abs">
  <h2 class="section-title" style="margin-top:35px">Using Data for Success</h2>
  <div class="section-kicker">Search engine optimization has been replaced with search experience optimization</div>
  <p>SALES is the end result of everything we do. It is why companies exists. It's why we market. It's why your business is online. Our job is to help you maximize your opportunity online to build your brand, get found by new customers and, ultimately, generate SALES! We thrive on data. It's digital quantum mechanics! We immerse ourselves in metrics, analytics, and insights to continually improve each marketing initiative. We are nimble and can respond quickly to opportunities we see in the data. There is no room for complacency online!<br>How well are you responding to the ever evolving digital landscape? Are you taking advantage of the tremendous sales opportunities in front of you? It's time to find out. Let us put together an objective snapshot of your digital presence... <a>READ MORE+</a></p>
  <div class="stat-rings">
    <div class="ring" style="left:0">
      <svg width="110" height="110" viewBox="0 0 110 110"><circle cx="55" cy="55" r="51" fill="none" stroke="#e2e6ea" stroke-width="4"/><circle cx="55" cy="55" r="51" fill="none" stroke="var(--blue)" stroke-width="4" stroke-dasharray="298 320" transform="rotate(-90 55 55)"/></svg>
      <div class="ring-value">93%</div>
      <div class="ring-label">Online Experiences<br>begin with a search Engine</div>
    </div>
    <div class="ring" style="left:240px">
      <svg width="110" height="110" viewBox="0 0 110 110"><circle cx="55" cy="55" r="51" fill="none" stroke="#e2e6ea" stroke-width="4"/><circle cx="55" cy="55" r="51" fill="none" stroke="var(--blue)" stroke-width="4" stroke-dasharray="224 320" transform="rotate(-90 55 55)"/></svg>
      <div class="ring-value">70%</div>
      <div class="ring-label">Of the links search users click<br>on are organic</div>
    </div>
    <div class="ring" style="left:494px">
      <svg width="110" height="110" viewBox="0 0 110 110"><circle cx="55" cy="55" r="51" fill="none" stroke="#e2e6ea" stroke-width="4"/><circle cx="55" cy="55" r="51" fill="none" stroke="var(--blue)" stroke-width="4" stroke-dasharray="298 320" transform="rotate(-90 55 55)"/></svg>
      <div class="ring-value">93%</div>
      <div class="ring-label">Of US population has at least one<br>social networking profile</div>
    </div>
    <div class="ring" style="left:766px;width:260px">
      <svg width="110" height="110" viewBox="0 0 110 110"><circle cx="55" cy="55" r="51" fill="none" stroke="#e2e6ea" stroke-width="4"/><circle cx="55" cy="55" r="51" fill="none" stroke="var(--blue)" stroke-width="4" stroke-dasharray="160 320" transform="rotate(-90 55 55)"/></svg>
      <div class="ring-value">50%</div>
      <div class="ring-label">Of companies are using digital marketing<br>but don't have a plan</div>
    </div>
  </div>
</section>

<section class="prism abs">
  <h2>FREE ONLINE PRISM CHECK</h2>
  <p>Sed ut perspiciatis unde omnis iste natus error sit voluptatem accusantium doloremque laudantium, totam rem aperiam, eaque ipsa quae ab illo inventore veritatis et quasi architecto beatae vitae dicta sunt explicabo. Nemo enim ipsam voluptatem quia voluptas sit aspernatur aut odit aut fugit, sed quia...</p>
  <div class="actions"><span>READ MORE INFO!</span><span>START TRIAL TODAY!</span></div>
</section>

<section class="formula abs">
  <h2 class="section-title">Digital Marketing Formula!</h2>
  <div class="section-kicker">Get the right message in front of the right people...</div>
  <div class="formula-visual" role="img" aria-label="Desktop monitor showing a glowing network world map above a tablet"></div>
  <div class="service" style="top:140px">
    <div class="service-icon"><svg width="30" height="22" viewBox="0 0 30 22"><rect x="5" y="2" width="20" height="14" fill="none" stroke="#fff" stroke-width="2"/><path d="M1 20h28" stroke="#fff" stroke-width="2"/></svg></div>
    <div><h3>Website</h3><p>You've got 10 seconds to grab the attention of a site viewer. We build for appearance, content, and functionality. It's a conversion causal nexus!</p></div>
  </div>
  <div class="service" style="top:262px">
    <div class="service-icon"><svg width="26" height="26" viewBox="0 0 26 26"><rect x="2" y="5" width="18" height="18" fill="none" stroke="#fff" stroke-width="2"/><path d="M10 16l2-5 11-10 3 3-11 10z" fill="#fff"/></svg></div>
    <div><h3>Content</h3><p>Content is the most powerful element of our formula... it creates need, provokes emotion and sparks action.</p></div>
  </div>
  <div class="service" style="top:384px">
    <div class="service-icon"><svg width="26" height="26" viewBox="0 0 26 26"><circle cx="13" cy="13" r="11" fill="none" stroke="#fff" stroke-width="2"/><path d="M8 7c3 1 2 4 5 5s1 5 3 7M17 4c-1 3 2 4 5 5" stroke="#fff" stroke-width="2" fill="none"/></svg></div>
    <div><h3>Social</h3><p>We are obsessed with the latest trends and are always testing new ways to cultivate both following and engagement.</p></div>
  </div>
</section>

<section class="numbers abs">
  <div class="number" style="left:215px">
    <svg width="40" height="40" viewBox="0 0 40 40"><rect x="4" y="7" width="32" height="29" fill="none" stroke="#fff" stroke-width="3"/><path d="M4 15h32M12 3v8M28 3v8M11 21h4M18 21h4M25 21h4M11 28h4M18 28h4M25 28h4" stroke="#fff" stroke-width="3"/></svg>
    <strong>35 YEARS</strong><h4>Combined Marketing Experience</h4>
    <p>Accusantium doloremque laudantium, tota me rem aperiam, eaque ipsa quae ab illo totis et quasi architecto...</p>
  </div>
  <div class="number" style="left:475px">
    <svg width="40" height="40" viewBox="0 0 40 40"><circle cx="16" cy="16" r="11" fill="none" stroke="#fff" stroke-width="4"/><path d="M24 24l12 12" stroke="#fff" stroke-width="5"/></svg>
    <strong>10 YEARS</strong><h4>Search Engine Optimization<br>Experience</h4>
    <p>Accusantium doloremque laudantium, toto totis et quasi architecto...</p>
  </div>
  <div class="number" style="left:740px">
    <svg width="40" height="40" viewBox="0 0 40 40"><rect x="3" y="5" width="34" height="30" fill="none" stroke="#fff" stroke-width="3"/><path d="M7 31l9-11 6 7 4-4 7 8z" fill="#fff"/><circle cx="27" cy="13" r="3" fill="#fff"/></svg>
    <strong>234</strong><h4>Websites Created</h4>
    <p>Accusantium doloremque laudantium, toto me rem aperiam, eaque ipsa quae ab illo totis et quasi architecto...</p>
  </div>
  <div class="number" style="left:995px">
    <svg width="44" height="40" viewBox="0 0 44 40"><circle cx="22" cy="11" r="7" fill="#fff"/><path d="M10 36c0-10 5-15 12-15s12 5 12 15z" fill="#fff"/><circle cx="8" cy="15" r="5" fill="#fff"/><circle cx="36" cy="15" r="5" fill="#fff"/><path d="M0 34c0-7 3-11 8-11s7 3 7 5l-3 6zM44 34c0-7-3-11-8-11s-7 3-7 5l3 6z" fill="#fff"/></svg>
    <strong>01</strong><h4>Amazing Team</h4>
    <p>Accusantium doloremque laudantium, toto me rem aperiam, eaque ipsa quae ab illo totis et quasi architecto...</p>
  </div>
</section>

<section class="snapshot abs">
  <h2>Let us put together an objective snapshot of your digital presence for you.</h2>
  <p>Sed ut perspiciatis unde omnis iste natus error sit voluptatem accusantium doloremque laudantium, totam rem aperiam, eaque ipsa quae ab illo inventore veritatis et quasi architecto beatae vitae dicta sunt explicabo. Nemo enim ipsam voluptatem quia voluptas sit aspernatur aut odit aut fugit, sed quia consequuntur magni dolores eos qui ratione voluptatem sequi nesciunt. Neque porro quisquam est, qui dolorem ipsum quia dolor sit amet, consectetur, adipisci velit...</p>
  <p style="margin-top:14px">Sed quia non numquam eius modi tempora incidunt ut labore et dolore magnam aliquam quaerat voluptatem. Ut enim ad minima veniam, quis nostrum exercitationem ullam corporis suscipit laboriosam, nisi ut aliquid ex ea commodi consequatur? Quis autem vel eum iure reprehenderit qui in ea voluptate velit esse quam nihil molestiae consequatur, vel illum qui dolorem eum fugiat but because those who do not know how to pursue pleasure rationally encounter consequences Nor again is there anyone who loves or pursues or desires to obtain pain of itself, because it is pain...</p>
  <div class="snapshot-device" role="img" aria-label="Smartphone displaying an analytics dashboard with bar, pie and area charts"></div>
</section>

<footer class="site-footer abs">
  <div class="brand"><span class="brand-mark"></span>Fernquill Digital Marketing</div>
  <div class="social"><span></span><span></span><span></span><span></span><span></span></div>
  <div class="footer-rule"></div>
  <div class="footer-col" style="left:96px">
    <h5>Quick Link</h5>
    <ul><li>Home</li><li>Marketing Catalysts</li><li>Our Formula</li><li>Chemical Reactions</li><li>Contact us</li></ul>
  </div>
  <div class="footer-col" style="left:330px">
    <h5>Contact Us</h5>
    <div class="contact-row" style="margin-top:20px"><svg width="12" height="16" viewBox="0 0 12 16"><path d="M6 0a6 6 0 0 0-6 6c0 4 6 10 6 10s6-6 6-10a6 6 0 0 0-6-6z" fill="#fff"/><circle cx="6" cy="6" r="2" fill="#0b0d10"/></svg><span>2870 W. Alder Avenue<br>Suite 210</span></div>
    <div class="contact-row"><svg width="12" height="14" viewBox="0 0 12 14"><path d="M2 0l3 3-1.5 2c1 2 2.5 3.5 4.5 4.5L10 8l2 3-2 3C5 13 0 8 0 2z" fill="#fff"/></svg><span>Phone : 866-555-0142</span></div>
    <div class="contact-row"><svg width="14" height="12" viewBox="0 0 14 12"><rect y="1" width="14" height="10" fill="#fff"/><path d="M0 1l7 6 7-6" stroke="#0b0d10" fill="none"/></svg><span>info@fernquilldigital.com</span></div>
  </div>
  <div class="contact-form">
    <div class="field" style="left:0;top:0;width:225px">Name</div>
    <div class="field" style="left:237px;top:0;width:230px">Mail</div>
    <div class="field" style="left:0;top:44px;width:225px">Phone</div>
    <div class="field" style="left:237px;top:44px;width:230px">Subject</div>
    <div class="field" style="left:0;top:88px;width:467px;height:66px">Message</div>
    <div class="send">Send Message</div>
  </div>
</footer>

<div class="copyright abs">© 2016 . fernquilldigital.All Rights Reserved.<span class="code">C11</span></div>

</body>
</html>
```